new service company in the field of construction seeks to make the Creation of a PPT

We need a PPT format with a cover page a frame for presentation. our company is based in Paris which was named VORENTIX. we just did our logo attached. Our company offers services to manage and control documents that pass on projects in construction (building, infrastructure, energy, oil and gas etc. ..). We use internet systems to help us, design must show insurance, quality, and safety. Customers should build any type of works and can not build without the approved documents. These documents go through multiple validations, and vorentix staff seconded on projects, coordinate these processes and documents, quality documents, to ensure that project deadlines are met and project management sees his project developed within the period, through regular reporting. the services offered by our company help ensure the project of building on time, to ensure the project manager visibility on what e will not, and can act accordingly.

Target Market(s)

general contractor of engineering construction or big business masters lumber wholesale real estate investor, project ownership in the construction sector

Industry/Entity Type

Construction

Contact Information for Business Card

carte rectangulaire petite taille (4X6cm env)
horizontale ou verticale
prendre en compte les éléments suivants :
logo
nom de société
adresse postale (4 lignes)
teléphone:
mail
role (ex : directeur)
in the back : La qualité documentaire de vos projets

Font styles to use
Sans Serif

Colors
34a7d7
85cae6
cee9f5
0592cd

Requirements
Must have
• The project should have 2 sliders: slider 1. Cover Page 2. slider for the content of presentations THE GOAL IS TO HAVE A VISUAL IDENTITY ON PPT, MY BUSINESS CARDS AND LETTERS must stay in mind and colors of the logo that joined the design must be clean and recall the seriousness, ease. the design must take into account the page numbers Tag line: the documentary quality of your projects information such as tagline and writes must be modifiable
Nice to have
• would require the presentation of the figure shows concepts or reporting table THE GOAL IS TO HAVE A VISUAL IDENTITY ON PPT, MY BUSINESS CARDS AND LETTERS
Should not have
• not to building or building in the logo

```html
<!DOCTYPE html>
<html lang="en">
<head>
<meta charset="utf-8">
<title>Vorentix – Cover Slide</title>
<link rel="stylesheet" href="https://fonts.googleapis.com/css2?family=Montserrat:wght@500;600&family=Raleway:wght@600;700&display=swap">
<style>
  :root {
    --brand-blue: #2f72b5;
    --headline-grey: #575757;
    --band-white: #ffffff;
    --tagline-white: #ffffff;
    --bg-mint: #d4ecd1;
    --bg-teal: #8fcfc4;
    --bg-slate: #86a9bb;
    --bg-sky: #3fa3d0;
    --bg-deep: #1f6fb0;
    --bg-haze: #93b6c8;
  }
  * { margin: 0; padding: 0; box-sizing: border-box; }
  html, body { width: 1200px; height: 662px; overflow: hidden; background: #fff; }
  .slide {
    position: relative;
    width: 1200px;
    height: 662px;
    overflow: hidden;
  }
  .slide__backdrop {
    position: absolute;
    inset: 0;
    background:
      radial-gradient(ellipse 60% 55% at 8% 0%, var(--bg-mint) 0%, rgba(212,236,209,0) 70%),
      radial-gradient(ellipse 55% 50% at 100% 0%, var(--bg-slate) 0%, rgba(134,169,187,0) 75%),
      radial-gradient(ellipse 60% 60% at 100% 100%, var(--bg-deep) 0%, rgba(31,111,176,0) 80%),
      radial-gradient(ellipse 50% 50% at 60% 65%, var(--bg-sky) 0%, rgba(63,163,208,0) 75%),
      radial-gradient(ellipse 50% 55% at 0% 100%, var(--bg-haze) 0%, rgba(147,182,200,0) 80%),
      linear-gradient(135deg, var(--bg-mint) 0%, var(--bg-teal) 40%, var(--bg-sky) 75%, var(--bg-deep) 100%);
  }
  .title-band {
    position: absolute;
    left: 0;
    top: 118px;
    width: 1200px;
    height: 212px;
    background: var(--band-white);
  }
  .brand {
    position: absolute;
    left: 58px;
    top: 236px;
    display: flex;
    align-items: center;
    gap: 14px;
  }
  .brand__dot {
    width: 22px;
    height: 22px;
    border-radius: 50%;
    background: var(--brand-blue);
  }
  .brand__name {
    font-family: "Montserrat", sans-serif;
    font-weight: 600;
    font-size: 58px;
    line-height: 1;
    letter-spacing: 1px;
    color: var(--brand-blue);
  }
  .headline {
    position: absolute;
    left: 456px;
    top: 190px;
    font-family: "Raleway", sans-serif;
    font-weight: 600;
    font-size: 37px;
    line-height: 1;
    color: var(--headline-grey);
    letter-spacing: 0.3px;
  }
  .tagline {
    position: absolute;
    right: 28px;
    top: 556px;
    text-align: right;
    font-family: "Raleway", sans-serif;
    font-weight: 700;
    font-size: 35px;
    line-height: 41px;
    color: var(--tagline-white);
    letter-spacing: 0.5px;
  }
  .tagline__line { display: block; }
</style>
</head>
<body>
  <main class="slide">
    <div class="slide__backdrop" role="img" aria-label="Low-poly triangular mosaic background fading from mint green at top left to deep blue at bottom right"></div>
    <section class="title-band">
    </section>
    <div class="brand">
      <span class="brand__name">VORENTIX</span>
      <span class="brand__dot"></span>
    </div>
    <h1 class="headline">HEADLINE OF YOUR BUSINESS</h1>
    <p class="tagline">
      <span class="tagline__line">MANAGE AND CONTROL DOCUMENTS</span>
      <span class="tagline__line">THAT PASS ON PROJECTS IN CONSTRUCTIONON</span>
    </p>
  </main>
</body>
</html>
```